Business Card Design - ChoiceCraft

Looking for creative, modern design, two sided for ChoiceCraft that is consistent with color and feel of website www.choicecraftpro.net.
Updates

Back of card will be used to promote products or have a quote revolving around decisions, change, leadership, innovation, creativity. Back should also have space to promote website, but optional to use the icon. Front of the card will need to use the icon and have standard place for name, job title, phone and email. We are not looking to put a mailing address or fax. Also want space to place a few words/phrase explaining what we do...such as individual growth and organizational development or tools, training, information...in addition, want the facebook icon small on the front somewhere as we are also on facebook.

Vector file uploaded of icon.

Target Market(s)

Professional coaching for individual growth and organizational development

Industry/Entity Type

Business

Requirements
Must have
• Icon...see attached.

```html
<!DOCTYPE html>
<html lang="en">
<head>
<meta charset="utf-8">
<title>ChoiceCraft Business Card</title>
<link rel="stylesheet" href="https://fonts.googleapis.com/css2?family=Open+Sans:wght@400;600;700&family=Arimo:wght@400;700&display=swap">
<style>
  :root {
    --stage: #1c1c1e;
    --card-white: #ffffff;
    --brand-blue: #1a7fd0;
    --brand-deep: #0e63b4;
    --brand-light: #3fb4ec;
    --silver: #aeb6c4;
    --ink: #2a2a2a;
    --muted: #6a6a6a;
    --quote-text: #ffffff;
  }
  * { box-sizing: border-box; margin: 0; padding: 0; }
  html, body { width: 1200px; height: 761px; overflow: hidden; }
  body {
    background: var(--stage);
    font-family: "Open Sans", Arial, sans-serif;
    position: relative;
  }
  .card {
    position: absolute;
    top: 220px;
    width: 540px;
    height: 320px;
    overflow: hidden;
    box-shadow: 0 10px 30px rgba(0,0,0,.5);
  }
  .card-front { left: 40px; background: var(--card-white); }
  .card-back {
    left: 620px;
    background: radial-gradient(ellipse at 50% 45%, #5ab4ea 0%, var(--brand-blue) 45%, var(--brand-deep) 100%);
  }

  /* front */
  .front-wave { position: absolute; left: 0; top: 0; width: 540px; height: 320px; }
  .brand {
    position: absolute; left: 30px; top: 70px; width: 180px;
    display: flex; flex-direction: column; align-items: center; gap: 12px;
  }
  .brand-dot {
    width: 86px; height: 86px; border-radius: 50%;
    background: var(--brand-blue);
  }
  .brand-name { font-size: 17px; font-weight: 400; color: var(--ink); }
  .divider {
    position: absolute; left: 224px; top: 50px; width: 1px; height: 140px;
    background: linear-gradient(var(--card-white), #b9bec6, var(--card-white));
  }
  .contact { position: absolute; left: 244px; top: 48px; }
  .person-name { font-size: 22px; font-weight: 700; color: var(--brand-deep); line-height: 1.1; }
  .person-title { font-size: 14px; color: var(--muted); margin: 4px 0 10px; }
  .contact-list { list-style: none; font-size: 13px; color: var(--ink); line-height: 1.35; }
  .contact-list li { display: flex; align-items: center; gap: 6px; }
  .contact-list svg { width: 11px; height: 11px; flex: none; }
  .social-square { width: 10px; height: 10px; background: var(--brand-deep); flex: none; }
  .tagline {
    position: absolute; left: 0; right: 0; bottom: 16px;
    text-align: center; color: #fff; font-size: 14.5px;
  }

  /* back */
  .back-mark {
    position: absolute; left: 210px; top: 100px; width: 120px; height: 120px;
    border-radius: 50%; background: rgba(255,255,255,.08);
  }
  .quotes {
    position: absolute; inset: 14px 10px; list-style: none;
    display: flex; flex-direction: column; justify-content: space-between;
    text-align: center; font-family: "Arimo", Arial, sans-serif; color: var(--quote-text);
  }
  .quote-text { font-size: 13.5px; line-height: 1.2; }
  .quote-text::before { content: "\201C"; font-size: 20px; font-weight: 700; vertical-align: -4px; margin-right: 1px; }
  .quote-text::after { content: "\201D"; font-size: 20px; font-weight: 700; vertical-align: -8px; margin-left: 1px; }
  .quote-author { font-size: 13.5px; font-weight: 700; }
</style>
</head>
<body>
  <section class="card card-front" aria-label="Card front">
    <svg class="front-wave" viewBox="0 0 540 320" aria-hidden="true">
      <defs>
        <linearGradient id="band" x1="0" y1="0" x2="1" y2="0">
          <stop offset="0" stop-color="var(--brand-light)"/>
          <stop offset="1" stop-color="var(--brand-deep)"/>
        </linearGradient>
      </defs>
      <path d="M0 232 C160 268 340 240 540 170 L540 320 L0 320 Z" fill="var(--silver)" opacity=".6"/>
      <path d="M0 242 C170 274 350 250 540 182 L540 320 L0 320 Z" fill="url(#band)"/>
    </svg>

    <div class="brand">
      <span class="brand-dot"></span>
      <span class="brand-name">ChoiceCraft</span>
    </div>

    <div class="divider"></div>

    <div class="contact">
      <p class="person-name">Your Name</p>
      <p class="person-title">Title</p>
      <ul class="contact-list">
        <li><svg viewBox="0 0 12 12"><path d="M2.5 1 L4.5 1 L5.2 3.5 L4 4.5 C4.6 6 6 7.4 7.5 8 L8.5 6.8 L11 7.5 L11 9.5 C11 10.3 10.3 11 9.5 11 C5 11 1 7 1 2.5 C1 1.7 1.7 1 2.5 1 Z" fill="var(--ink)"/></svg>123-456-789</li>
        <li><svg viewBox="0 0 12 12"><rect x="1" y="2.5" width="10" height="7" fill="none" stroke="var(--ink)" stroke-width="1.2"/><path d="M1 2.5 L6 6.5 L11 2.5" fill="none" stroke="var(--ink)" stroke-width="1.2"/></svg>info@choicecraftpro.net</li>
        <li><svg viewBox="0 0 12 12"><circle cx="6" cy="6" r="5" fill="none" stroke="var(--ink)" stroke-width="1.1"/><ellipse cx="6" cy="6" rx="2.2" ry="5" fill="none" stroke="var(--ink)" stroke-width="1"/><path d="M1 6 H11" stroke="var(--ink)" stroke-width="1"/></svg>www.choicecraftpro.net</li>
        <li><span class="social-square"></span>/choicecraftpro</li>
      </ul>
    </div>

    <p class="tagline">Supporting individual growth &amp; organizational development.</p>
  </section>

  <section class="card card-back" aria-label="Card back">
    <div class="back-mark"></div>
    <ul class="quotes">
      <li><p class="quote-text">Try not to become a man of success, but rather a man of value.</p><p class="quote-author">- Arlen Westbrook</p></li>
      <li><p class="quote-text">The only constant is change.</p><p class="quote-author">- Theron Vale</p></li>
      <li><p class="quote-text">We are what we repeatedly do. Excellence is not an act, it is a habit.</p><p class="quote-author">- Cassian Dorne</p></li>
      <li><p class="quote-text">Simplicity is the ultimate sophistication.</p><p class="quote-author">- Lorenzo Marelli</p></li>
      <li><p class="quote-text">Life is not fair - get used to it.</p><p class="quote-author">- Wade Hollis</p></li>
    </ul>
  </section>
</body>
</html>
```